Dental Practice Billboard Design

We are a newer dental practice in need of a simple but appealing billboard for our growing dental practice to attract new patients. The practice is owned by husband and wife dentists and is family friendly in a small town in Kentucky. We try to be very friendly and caring to our patients. Would prefer a blue background for the billboard and our tooth logo to be prominent. We are partial to the Patua One font used in the image below but please feel free to tweak it as you deem necessary. The shape of the uppercase D and lowercase g are why we like that font, so fonts with a similarly shaped “D” and “g” would work as well. Please include our phone number (555) 847-1390. Please see our website Harlowbrookdentistry.example for more info on the practice if needed. Thank you! Looking forward to seeing your creation.
Updates

The dimensions will be 12ft x 24ft (3.6576m x 7.3152m). Apologies for not including this in the original prompt. Thank you all for your submissions.

Industry/Entity Type

Dental

Font styles to use
Other font styles liked:
• Patua One

Colors
0054AA
0677BA
7BADD7
CADEEF
E8F1F8
0094D4
00A9DD
6FCCEA
C7EBF8
E9F6FB
00AB8E
00BBA5
67D7C9
C6EFE9
E9F9F6
59FF00
82FF00
B8FF75
E3FFCB
F4FFEA

Requirements
Must have
• Phone number, website, Logo, Practice name “Harlow Brook Dentistry”
Should not have
• A tagline or slogan

```html
<!DOCTYPE html>
<html lang="en">
<head>
<meta charset="utf-8">
<title>Harlow Brook Dentistry Billboard</title>
<link rel="stylesheet" href="https://fonts.googleapis.com/css2?family=Patua+One&display=swap">
<style>
  :root {
    --navy: #1b2b55;
    --green: #2bb24c;
    --white: #ffffff;
  }
  * { margin: 0; padding: 0; box-sizing: border-box; }
  html, body {
    width: 1200px;
    height: 625px;
    overflow: hidden;
    background: var(--navy);
  }
  .billboard {
    position: relative;
    width: 1200px;
    height: 625px;
    background: var(--navy);
    font-family: "Patua One", Georgia, serif;
    color: var(--white);
  }
  .brand-mark {
    position: absolute;
    left: 60px;
    top: 90px;
    width: 380px;
    height: 430px;
    display: flex;
    flex-direction: column;
    align-items: center;
    justify-content: center;
    gap: 28px;
  }
  .brand-mark__circle {
    width: 250px;
    height: 250px;
    border-radius: 50%;
    background: var(--green);
  }
  .brand-mark__name {
    font-size: 36px;
    line-height: 1;
    color: var(--white);
  }
  .practice-name {
    position: absolute;
    left: 478px;
    top: 124px;
    font-size: 96px;
    line-height: 1;
    font-weight: 400;
    letter-spacing: -0.5px;
    white-space: nowrap;
  }
  .practice-subtitle {
    position: absolute;
    left: 480px;
    top: 236px;
    font-size: 40px;
    line-height: 1;
    font-weight: 400;
  }
  .phone-pill {
    position: absolute;
    left: 480px;
    top: 330px;
    width: 520px;
    height: 107px;
    border-radius: 54px;
    background: var(--green);
    display: flex;
    align-items: center;
    padding-left: 42px;
    gap: 12px;
  }
  .phone-pill__icon {
    width: 36px;
    height: 52px;
    flex: none;
  }
  .phone-pill__number {
    font-size: 54px;
    line-height: 1;
    color: var(--white);
    white-space: nowrap;
  }
  .website {
    position: absolute;
    left: 480px;
    top: 484px;
    font-size: 37px;
    line-height: 1;
    font-weight: 400;
    white-space: nowrap;
  }
</style>
</head>
<body>
  <main class="billboard">
    <div class="brand-mark">
      <div class="brand-mark__circle"></div>
      <span class="brand-mark__name">Harlow Brook</span>
    </div>

    <h1 class="practice-name">Harlow Brook</h1>
    <p class="practice-subtitle">Dentistry</p>

    <div class="phone-pill">
      <svg class="phone-pill__icon" viewBox="0 0 36 52" aria-hidden="true">
        <path fill="#1b2b55" d="M20 2c3 0 6 1 7 3l-4 11c-1 2-4 2-6 2-3 5-4 11-3 16 2 0 5 1 5 3l-1 11c-1 2-4 3-7 3C5 49 3 40 4 30 5 18 10 6 20 2z"/>
      </svg>
      <span class="phone-pill__number">(555) 847-1390</span>
    </div>

    <p class="website">Harlowbrookdentistry.example</p>
  </main>
</body>
</html>
```